Varentoria Business Card and Letter Head

We are a leadership assessment consultancy based in Sydney, Australia. We help executive-level decison-makers select leaders for more senior level roles in corporate and government organisations. Our methodology is based on the latest research from the field of neuroscience.
We need a business card design and matching letter head that presents our company, Varentoria, as a:
1. trusted adviser to senior executive-level decison makers
2. niche consultancy who are experts in the field of assessing leadership talent
3. results-focused solution provider who balance scientific methods with pragmatic solutions
The following company details should be used in all designs:
Company Name: Varentoria
Details (for business card):
Derek Hanford
Prime Capacity Officer
Level 29, Marlow Tower
7 Marlow Square
Sydney, NSW 2000 Australia
Phone: 1300 582 714
Mobile: 0412 637 258
Email: derek.hanford@varentoria-example.com.au
Website: varentoria-example.com.au
I have attached the logo for Varentoria (for both a white and black background) - your business card and letter head designs must incoporate this logo and colour scheme.
Thanks for your interest in this project, I'm looking forward to receiving your ideas.
Regards,
Derek
Target Market(s)
Executive-level decison-makers in corporate and government organisations (e.g., CEO, VP, Head of Human Resources)
Industry/Entity Type
Leadership
Look and feel

```html
<!DOCTYPE html>
<html lang="en">
<head>
<meta charset="utf-8">
<title>Varentoria Business Card</title>
<link href="https://fonts.googleapis.com/css2?family=Open+Sans:wght@400;600;700&display=swap" rel="stylesheet">
<style>
  :root {
    --brand-red: #b8261b;
    --ink: #3b3b3b;
    --ink-soft: #555555;
    --faint: #ececec;
    --card: #ffffff;
    --backdrop: #e8e6e3;
    --on-red: #ffffff;
  }
  * { box-sizing: border-box; margin: 0; padding: 0; }
  html, body {
    width: 1200px; height: 1094px; overflow: hidden;
    background: var(--backdrop);
    font-family: "Open Sans", Arial, sans-serif;
    color: var(--ink);
  }
  .stage { position: relative; width: 1200px; height: 1094px; }
  .card {
    position: absolute; width: 760px; height: 440px;
    background: var(--card); border-radius: 28px; overflow: hidden;
    box-shadow: 0 6px 18px rgba(0,0,0,0.12);
  }
  .card--front { left: 90px; top: 70px; }
  .card--back { left: 350px; top: 580px; }

  .brand { display: flex; align-items: center; gap: 14px; }
  .brand__square { background: var(--brand-red); flex: none; }
  .brand__name { font-weight: 700; color: var(--ink); letter-spacing: -0.5px; line-height: 1; }

  .card--front .brand { position: absolute; left: 46px; top: 66px; }
  .card--front .brand__square { width: 34px; height: 34px; }
  .card--front .brand__name { font-size: 44px; }

  .faint-square {
    position: absolute; right: 70px; top: 34px; width: 150px; height: 150px;
    border: 18px solid var(--faint);
  }

  .wave { position: absolute; left: 0; top: 0; width: 760px; height: 440px; }

  .person { position: absolute; left: 46px; top: 196px; }
  .person__name { color: var(--brand-red); font-weight: 700; font-size: 22px; }
  .person__title { font-size: 15px; color: var(--ink); margin-top: 2px; }

  .contacts { position: absolute; left: 46px; top: 270px; list-style: none; }
  .contacts li { display: flex; align-items: center; gap: 9px; font-size: 15px; line-height: 22px; color: var(--ink); }
  .contacts svg { width: 14px; height: 14px; flex: none; fill: var(--ink-soft); }

  .address {
    position: absolute; right: 40px; top: 330px; text-align: right;
    color: var(--on-red); font-size: 15px; line-height: 23px; font-style: normal;
  }

  .card--back .brand { position: absolute; left: 110px; top: 120px; gap: 24px; }
  .card--back .brand__square { width: 64px; height: 64px; }
  .card--back .brand__name { font-size: 92px; }
  .web {
    position: absolute; left: 0; right: 0; top: 320px; text-align: center;
    color: var(--brand-red); font-size: 26px; letter-spacing: 3px;
  }
</style>
</head>
<body>
<main class="stage">
  <section class="card card--front" aria-label="Business card front">
    <div class="faint-square" aria-hidden="true"></div>
    <div class="brand">
      <span class="brand__square" aria-hidden="true"></span>
      <span class="brand__name">Varentoria</span>
    </div>

    <svg class="wave" viewBox="0 0 760 440" aria-hidden="true">
      <path d="M0,372 C140,340 250,420 380,404 C480,392 580,230 760,190 L760,440 L0,440 Z" fill="var(--brand-red)"/>
      <path d="M240,402 C400,380 540,240 760,166 L760,180 C560,246 420,384 240,402 Z" fill="var(--ink)"/>
    </svg>

    <div class="person">
      <p class="person__name">Derek Hanford</p>
      <p class="person__title">Prime Capacity Officer</p>
    </div>

    <ul class="contacts">
      <li><svg viewBox="0 0 16 16"><path d="M3 1l3 3-1.5 2a9 9 0 0 0 5.5 5.5L12 10l3 3-2 2C7 15 1 9 1 3z"/></svg>1300 582 714</li>
      <li><svg viewBox="0 0 16 16"><path d="M4 0h8v16H4zM5.5 2v9h5V2z"/></svg>0412 637 258</li>
      <li><svg viewBox="0 0 16 16"><path d="M0 3h16v10H0zM1.5 4.5L8 9l6.5-4.5z"/></svg>derek.hanford@varentoria-example.com.au</li>
      <li><svg viewBox="0 0 16 16"><circle cx="8" cy="8" r="7.5"/></svg>www.varentoria-example.com.au</li>
    </ul>

    <address class="address">
      Level 29, Marlow Tower<br>
      7 Marlow Square<br>
      Sydney, NSW 2000 Australia
    </address>
  </section>

  <section class="card card--back" aria-label="Business card back">
    <div class="brand">
      <span class="brand__square" aria-hidden="true"></span>
      <span class="brand__name">Varentoria</span>
    </div>
    <p class="web">www.varentoria-example.com.au</p>
  </section>
</main>
</body>
</html>
```